A specialised Sport management needs a corporate brochure design

We are a specialized company in the management and consultancy of sports events. and need to have a company brochure
We provide the following services;
Event management
Venues management
Production
Ticketing
Consulting
Hospitality
Activity management
Event timing
Branding of event
Event supplies
We need a corporate profile design for our company to showcase the major events that we have covered , with images, information, statistics, surveys, products and services used. We want to highlight our professionalism and execution of the events, experience of the participants, spectators . How we have grown in the past few years and reached the international standards.
Objectives of the work:
To get sponsors and partners for future business and to present Tri-Crest
as not just a sports management company but also a professional sports
events management company.
You can check our website
www.tri-crest.example
Target Market(s)
Sponsors and corporate partners
Industry/Entity Type
Events
Requirements
Must have
- Must Have:
- - Very professional look
- -Some event images,Event information, statistics, surveys, products and services used. We want to highlight our professionalism and execution of the events (Attached)
Nice to have
- Similar momentom of the below design
- http://www.lumavent.example/wp-content/themes/lumavent/pdf/CP-2014-15-V10-Web.pdf

```html
<!DOCTYPE html>
<html lang="en">
<head>
<meta charset="utf-8">
<title>Tri-Crest – Corporate Brochure Spread</title>
<link rel="stylesheet" href="https://fonts.googleapis.com/css2?family=Josefin+Sans:wght@400;600&display=swap">
<style>
  :root {
    --backdrop: #e9e6e1;
    --paper: #ffffff;
    --charcoal: #2a2a2b;
    --teal-deep: #1f8f7e;
    --teal-light: #5fe0c0;
    --accent-orange: #f04e23;
    --heading-cyan: #55d3e6;
    --text-light: #f2f2f2;
    --brand-grey: #3a3a3a;
  }
  * { box-sizing: border-box; margin: 0; padding: 0; }
  html, body {
    width: 1200px; height: 509px; overflow: hidden;
    background: var(--backdrop);
    font-family: "Josefin Sans", sans-serif;
  }
  .spread {
    position: absolute; left: 27px; top: 22px;
    width: 1146px; height: 461px;
    background: var(--paper);
    box-shadow: 0 2px 6px rgba(0,0,0,.25);
  }
  .spread-art { position: absolute; inset: 0; }
  .section-title {
    position: absolute; left: 583px;
    font-size: 17px; font-weight: 400; letter-spacing: .5px;
  }
  .about-title { top: 46px; color: var(--text-light); }
  .goal-title { top: 228px; color: var(--heading-cyan); }
  .section-body {
    position: absolute; left: 583px; width: 252px;
    color: var(--text-light);
    font-size: 10.4px; line-height: 13.6px;
    text-align: justify;
  }
  .section-body p + p { margin-top: 13px; }
  .about-body { top: 101px; }
  .goal-body { top: 280px; width: 280px; }
  .diagonal-edge {
    float: right;
    width: 110px; height: 170px;
    shape-outside: polygon(82px 0, 82px 29px, 1px 170px, 110px 170px, 110px 0);
  }
  .brand-badge {
    position: absolute; left: 928px; top: 238px;
    width: 170px; height: 170px; border-radius: 50%;
    background: var(--paper);
    display: flex; align-items: center; justify-content: center;
  }
  .brand-name {
    color: var(--brand-grey);
    font-size: 22px; font-weight: 600; letter-spacing: .5px;
  }
</style>
</head>
<body>
  <main class="spread">
    <svg class="spread-art" width="1146" height="461" viewBox="0 0 1146 461">
      <defs>
        <linearGradient id="photoTones" x1="0" y1="0" x2="0" y2="1">
          <stop offset="0" stop-color="#7fb3e6"/>
          <stop offset="0.28" stop-color="#b9cde0"/>
          <stop offset="0.42" stop-color="#b89a78"/>
          <stop offset="0.62" stop-color="#3d4d72"/>
          <stop offset="0.8" stop-color="#2d5a8a"/>
          <stop offset="1" stop-color="#143d6b"/>
        </linearGradient>
        <linearGradient id="tealPanel" x1="0" y1="0" x2="1" y2="1">
          <stop offset="0" stop-color="var(--teal-deep)"/>
          <stop offset="1" stop-color="var(--teal-light)"/>
        </linearGradient>
      </defs>

      <g role="img" aria-label="Photograph of triathletes in yellow swim caps running into the sea at the race start">
        <polygon points="0,0 306,0 410,165 570,445 570,461 0,461" fill="url(#photoTones)"/>
      </g>
      <polygon points="306,0 570,0 570,445 410,165" fill="var(--paper)"/>
      <polygon points="318,0 476,0 412,158" fill="url(#tealPanel)"/>
      <polygon points="0,312 0,461 320,461" fill="var(--paper)"/>
      <polygon points="62,362 240,461 48,461" fill="var(--accent-orange)"/>

      <rect x="570" y="0" width="576" height="461" fill="var(--charcoal)"/>
      <polygon points="1024,0 1146,0 1146,461 760,461" fill="url(#tealPanel)"/>
    </svg>

    <h2 class="section-title about-title">ABOUT US</h2>
    <div class="section-body about-body">
      <p>Tri-Crest is the leading company in Kuwait, which specializes in the management and consultancy of sports events. Established in 2007. Tri-Crest has grown in stature and strength over the years, to become the reowned establishment it is today in this highly specialized field.</p>
    </div>

    <h2 class="section-title goal-title">OUR GOAL</h2>
    <div class="section-body goal-body">
      <div class="diagonal-edge"></div>
      <p>Raise awareness of sport practice and creating exciting sport events with international standards. Allowing every individual to participate in different types of sport events for all levels.</p>
      <p>Each year we get closer to our goal to promote active lifestyle and sports activities in the country. We believe our partners play a major role in the contribution towards our goal for the society.</p>
    </div>

    <div class="brand-badge">
      <span class="brand-name">Tri-Crest</span>
    </div>
  </main>
</body>
</html>
```